Need help in designing new business card utilizing our new logo.

BuildMark Solutions works with Construction Business Owners, Managers & IT Professionals to strengthen software usage and increase user productivity.

Our Construction Accounting and Mobile Field Management Software Clients engage with us in the following areas:

New Software Implementations
Software Re-Implementations
Redesigning Software Usage at the User Level
Project Coordination & Management
Continued Software Support

Old tag line:
Weighing Options - Implementing Solutions

www.buildmark-solutions.example

Ridge 4 is a product, but not needed for a new business card.

```html
<!DOCTYPE html>
<html lang="en">
<head>
<meta charset="utf-8">
<title>BuildMark Solutions – Business Card</title>
<link rel="stylesheet" href="https://fonts.googleapis.com/css2?family=Open+Sans:wght@400;600;700;800&display=swap">
<style>
  :root {
    --bg: #e6e6e8;
    --card-dark: #333335;
    --card-dark-soft: #3b3b3e;
    --card-light: #ffffff;
    --brand-blue: #2b2f9e;
    --text-dark: #222226;
    --text-mid: #3a3a3e;
    --text-light: #f2f2f2;
    --text-grey: #c8c8cc;
  }
  * { box-sizing: border-box; margin: 0; padding: 0; }
  html, body { width: 1200px; height: 800px; overflow: hidden; }
  body {
    background: var(--bg);
    font-family: "Open Sans", Arial, sans-serif;
    position: relative;
  }
  .card {
    position: absolute;
    left: 300px;
    width: 600px;
    height: 343px;
    overflow: hidden;
    box-shadow: 0 6px 18px rgba(0,0,0,.18);
  }
  .card-front { top: 36px; background: var(--card-dark); }
  .card-back  { top: 421px; background: var(--card-light); }
  .card-shape { position: absolute; inset: 0; width: 100%; height: 100%; }

  /* front */
  .brand-lockup {
    position: absolute;
    left: 150px; top: 112px;
    display: flex; align-items: center; gap: 18px;
  }
  .brand-mark { width: 22px; height: 22px; background: var(--brand-blue); }
  .brand-rule { width: 2px; height: 74px; background: var(--brand-blue); }
  .brand-name {
    color: var(--text-grey);
    font-weight: 700;
    font-size: 34px;
    line-height: 1.05;
    letter-spacing: 1px;
    text-transform: uppercase;
  }
  .brand-name span { display: block; font-size: 21px; letter-spacing: 9px; }
  .front-web {
    position: absolute;
    right: 26px; top: 282px;
    font-size: 13px; color: var(--text-dark);
    white-space: nowrap;
  }
  .front-web b { color: var(--brand-blue); font-weight: 600; }

  /* back */
  .side-brand {
    position: absolute;
    left: 30px; top: 40px;
    width: 170px; height: 270px;
  }
  .side-name {
    position: absolute;
    left: 88px; top: 0;
    transform-origin: left top;
    transform: rotate(-90deg) translateX(-200px);
    color: var(--text-light);
    font-weight: 700;
    font-size: 31px;
    line-height: 1.05;
    white-space: nowrap;
    text-transform: uppercase;
    letter-spacing: 1px;
  }
  .side-name span { display: block; font-size: 18px; letter-spacing: 8px; }
  .side-mark {
    position: absolute;
    left: 70px; top: 222px;
    width: 30px; height: 30px;
    background: var(--text-light);
  }
  .contact-block {
    position: absolute;
    left: 275px; top: 42px;
    color: var(--text-mid);
  }
  .person-name {
    font-size: 25px; font-weight: 800; color: var(--text-dark);
    letter-spacing: .5px; text-transform: uppercase;
  }
  .person-title { font-size: 14px; font-weight: 700; color: var(--text-dark); margin-top: -2px; }
  .address { font-size: 13.5px; line-height: 1.45; margin-top: 52px; }
  .contact-list { list-style: none; margin-top: 18px; font-size: 13.5px; line-height: 1.6; }
  .contact-list li { display: flex; align-items: center; gap: 10px; white-space: nowrap; }
  .contact-list svg { width: 13px; height: 13px; fill: var(--brand-blue); flex: none; }
  .contact-list b { color: var(--brand-blue); font-weight: 600; }
</style>
</head>
<body>

<section class="card card-front" aria-label="Business card front">
  <svg class="card-shape" viewBox="0 0 600 343" preserveAspectRatio="none">
    <rect width="600" height="300" fill="var(--card-dark-soft)" opacity=".55" role="img" aria-label="Faint world map backdrop"/>
    <path d="M0 326 H270 C295 326 300 272 330 270 L600 262 V343 H0 Z" fill="var(--card-light)"/>
    <path d="M0 323 H270 C295 323 300 269 330 267" fill="none" stroke="var(--brand-blue)" stroke-width="6"/>
  </svg>
  <div class="brand-lockup">
    <div class="brand-mark"></div>
    <div class="brand-rule"></div>
    <div class="brand-name">BuildMark<span>Solutions</span></div>
  </div>
  <p class="front-web">www.<b>buildmark-solutions</b>.example</p>
</section>

<section class="card card-back" aria-label="Business card back">
  <svg class="card-shape" viewBox="0 0 600 343" preserveAspectRatio="none">
    <path d="M0 0 H205 C226 0 232 18 232 40 V343 H0 Z" fill="var(--card-dark)" role="img" aria-label="Dark panel with faint world map backdrop"/>
    <line x1="238" y1="60" x2="238" y2="343" stroke="var(--brand-blue)" stroke-width="5"/>
  </svg>

  <div class="side-brand">
    <div class="side-name">BuildMark<span>Solutions</span></div>
    <div class="side-mark"></div>
  </div>

  <div class="contact-block">
    <h1 class="person-name">Dana R. Whitfield</h1>
    <p class="person-title">Owner</p>
    <p class="address">48 Harbor Lane - Suite 12<br>Millbrook NY 12545</p>
    <ul class="contact-list">
      <li><svg viewBox="0 0 16 16"><path d="M3 1l3 3-1.5 2a9 9 0 0 0 5.5 5.5L12 10l3 3-2 2C7 15 1 9 1 3z"/></svg><span>800-555-0142 ext.100</span></li>
      <li><svg viewBox="0 0 16 16"><path d="M4 0h8a1 1 0 0 1 1 1v14a1 1 0 0 1-1 1H4a1 1 0 0 1-1-1V1a1 1 0 0 1 1-1zm1 2v10h6V2z"/></svg><span>555-014-2283</span></li>
      <li><svg viewBox="0 0 16 16"><path d="M0 3h16v10H0zM1.5 4.5L8 9l6.5-4.5z"/></svg><span>dana.w@buildmark-solutions.example</span></li>
      <li><svg viewBox="0 0 16 16"><path d="M7 1a6 6 0 1 1-4 10.5L0 15l1-4A6 6 0 0 1 7 1zm0 2a4 4 0 1 0 0 8 4 4 0 0 0 0-8z"/></svg><span>www.<b>buildmark-solutions</b>.example</span></li>
    </ul>
  </div>
</section>

</body>
</html>
```